Graphics Design of Physics Book

Hi
Size : 8" x 11.25"
We are education book Publication Company and would like to have book cover for "Physics" it has 4 volumes. All 4 having the same color scheme and design except the volume no.
Blue is my personal favorite but u can use any color. Want to have a band at the bottom of the cover to place our Logo “VORNA Education” a PDF of the same is attached, or you can place logo anywhere according to ur design.
I need “Physics” as title of the book to be visible prominently.
And volume and volume no. should also be Visible and eye catching I prefer a Graphic to enhance the Volume No.
A background pattern can also be a option (it should be vector form so that color can be change later)
Please do not offer any cut and paste design I need very professional presentation.
Volume and Number can be in metallic 3D (CMYK) effect.
only Professional presentation will get feedback.
I have provided a sample artwork for reference do not follow it but can be a reference what I needed !

Target Market(s)

Students Class 9th to 12th

Industry/Entity Type

Education

Font styles to use
Serif

Colors
3176b5
0555a3
85abd2
cadf82
abd036
9bcb3c

Requirements
Must have
• Eye catching.
• “Physics” as title of the book to be visible prominently.
• volume and volume no. should also be Visible and eye catching
• I prefer a Graphic to enhance the Volume No.
• Icons for
• 1. Questions and answers
• 2. Theory Notes
• 3. Tips & Tricks
• 4. Previous Year's Reference Questions
• 5. Covers Complete Syllabus
Nice to have
• decent seamless background or metallic 3d effect (not to be print in special Ink) design should only be in CMYK.
Should not have
• Physics related Pictures or Icons (Specially E=mc2) or any scientist photograph or I Need pure graphic design

```html
<!DOCTYPE html>
<html lang="en">
<head>
<meta charset="utf-8">
<title>Physics Volume 1 — Book Cover</title>
<link href="https://fonts.googleapis.com/css2?family=Archivo+Black&family=Open+Sans:wght@600;700;800&family=Playfair+Display:wght@900&display=swap" rel="stylesheet">
<style>
  :root{
    --cover-blue:#2f5aa3;
    --cover-blue-deep:#234785;
    --stripe-light:#3a67b0;
    --tile-blue:#7fa6d6;
    --tile-edge:#9dbbe2;
    --icon-ink:#2a2d33;
    --label:#ffffff;
    --silver-hi:#ffffff;
    --silver-mid:#c9cdd2;
    --silver-lo:#8d939a;
    --logo-ink:#2b2b2b;
  }
  html,body{margin:0;padding:0;overflow:hidden;background:#e9ebee;}
  .cover{
    position:relative;width:861px;height:1200px;overflow:hidden;
    background:var(--cover-blue);
    font-family:"Open Sans",sans-serif;
  }
  .title-band{
    position:absolute;left:0;top:0;width:861px;height:284px;
    background:repeating-linear-gradient(90deg,var(--cover-blue-deep) 0 48px,var(--stripe-light) 48px 96px);
    opacity:.9;
  }
  .title-rule{
    position:absolute;left:0;top:284px;width:861px;height:5px;
    background:linear-gradient(90deg,var(--silver-lo),var(--silver-hi),var(--silver-mid),var(--silver-hi),var(--silver-lo));
  }
  .title,.volume-word,.volume-number{position:absolute;left:0;top:0;}
  .features{
    position:absolute;left:0;top:816px;width:861px;height:170px;
  }
  .feature{
    position:absolute;top:0;width:150px;margin-left:-75px;text-align:center;
  }
  .feature-tile{
    width:104px;height:104px;margin:0 auto;border-radius:18px;
    background:linear-gradient(180deg,var(--tile-edge),var(--tile-blue));
    box-shadow:0 2px 0 rgba(0,0,0,.25),inset 0 0 0 2px rgba(255,255,255,.25);
    display:flex;align-items:center;justify-content:center;
  }
  .feature-tile svg{width:70px;height:70px;}
  .feature-label{
    margin-top:12px;color:var(--label);font-weight:600;font-size:19px;line-height:21px;
  }
  .logo-band{
    position:absolute;left:0;top:1074px;width:861px;height:66px;
    background:linear-gradient(90deg,var(--silver-lo),var(--silver-hi) 25%,var(--silver-mid) 50%,var(--silver-hi) 75%,var(--silver-lo));
    display:flex;align-items:center;justify-content:center;
  }
  .publisher-name{
    font-family:"Open Sans",sans-serif;font-weight:800;font-size:26px;letter-spacing:2px;
    color:var(--logo-ink);text-transform:uppercase;
  }
</style>
</head>
<body>
<div class="cover">
  <div class="title-band"></div>
  <div class="title-rule"></div>

  <svg class="title" width="861" height="300" viewBox="0 0 861 300">
    <defs>
      <linearGradient id="metal" x1="0" y1="0" x2="0" y2="1">
        <stop offset="0" stop-color="#ffffff"/>
        <stop offset=".35" stop-color="#b9bec5"/>
        <stop offset=".55" stop-color="#f4f5f6"/>
        <stop offset=".8" stop-color="#9aa0a7"/>
        <stop offset="1" stop-color="#e6e8ea"/>
      </linearGradient>
    </defs>
    <text x="32" y="233" font-family="Archivo Black, sans-serif" font-size="268" textLength="792" lengthAdjust="spacingAndGlyphs" fill="url(#metal)" stroke="#ffffff" stroke-width="2">Physics</text>
  </svg>

  <svg class="volume-word" width="861" height="440" viewBox="0 0 861 440">
    <text x="244" y="410" font-family="Open Sans, sans-serif" font-weight="800" font-size="112" textLength="380" lengthAdjust="spacingAndGlyphs" fill="url(#metal)">Volume</text>
  </svg>

  <svg class="volume-number" width="861" height="760" viewBox="0 0 861 760">
    <text x="380" y="724" font-family="Playfair Display, serif" font-weight="900" font-size="330" fill="#dfe3e8" opacity=".85">1</text>
    <text x="370" y="716" font-family="Playfair Display, serif" font-weight="900" font-size="330" fill="url(#metal)">1</text>
  </svg>

  <div class="features">
    <div class="feature" style="left:85px">
      <div class="feature-tile">
        <svg viewBox="0 0 70 70" fill="none" stroke="var(--icon-ink)" stroke-width="4" stroke-linejoin="round">
          <path d="M30 14h24a10 10 0 0 1 10 10v14a10 10 0 0 1-10 10h-4l6 8-12-8H40"/>
          <path d="M16 10h22a10 10 0 0 1 10 10v14a10 10 0 0 1-10 10H22l-12 8 4-9a10 10 0 0 1-8-10V20a10 10 0 0 1 10-10z" fill="var(--tile-edge)"/>
          <text x="10" y="34" font-family="Open Sans, sans-serif" font-weight="800" font-size="15" fill="var(--icon-ink)" stroke="none">Q&amp;A</text>
        </svg>
      </div>
      <div class="feature-label">Questions<br>&amp; Answers</div>
    </div>

    <div class="feature" style="left:256px">
      <div class="feature-tile">
        <svg viewBox="0 0 70 70" fill="none" stroke="var(--icon-ink)" stroke-width="4" stroke-linejoin="round" stroke-linecap="round">
          <rect x="12" y="12" width="38" height="50" rx="3"/>
          <path d="M24 12v-4h14v4"/>
          <path d="M18 24l3 3 5-6M30 24h14M18 36l3 3 5-6M30 36h14M18 48l3 3 5-6M30 48h6"/>
          <circle cx="52" cy="52" r="10" fill="var(--icon-ink)"/>
          <path d="M47 52l4 4 6-7" stroke="var(--tile-edge)"/>
        </svg>
      </div>
      <div class="feature-label">Complete<br>Syllabus</div>
    </div>

    <div class="feature" style="left:426px">
      <div class="feature-tile">
        <svg viewBox="0 0 70 70" fill="none" stroke="var(--icon-ink)" stroke-width="4" stroke-linecap="round" stroke-linejoin="round">
          <path d="M14 42a22 22 0 1 0 2-20"/>
          <path d="M10 18l6 6 6-6"/>
          <path d="M35 35l-6-8M35 35l10 8" stroke-width="5"/>
        </svg>
      </div>
      <div class="feature-label">Reference<br>Questions</div>
    </div>

    <div class="feature" style="left:598px">
      <div class="feature-tile">
        <svg viewBox="0 0 70 70" fill="none" stroke="var(--icon-ink)" stroke-width="4" stroke-linejoin="round" stroke-linecap="round">
          <path d="M42 14H12v44h44V30"/>
          <path d="M52 10l8 8-24 24-10 2 2-10z"/>
        </svg>
      </div>
      <div class="feature-label" style="padding-top:10px">Theory Notes</div>
    </div>

    <div class="feature" style="left:769px">
      <div class="feature-tile">
        <svg viewBox="0 0 70 70" fill="none" stroke="var(--icon-ink)" stroke-width="4" stroke-linecap="round" stroke-linejoin="round">
          <path d="M27 46c0-6-7-9-7-18a15 15 0 0 1 30 0c0 9-7 12-7 18z"/>
          <path d="M28 52h14M30 58h10"/>
          <path d="M35 4v6M14 12l4 4M56 12l-4 4M6 30h6M58 30h6M10 46l5-3M60 46l-5-3"/>
        </svg>
      </div>
      <div class="feature-label">Tips &amp; Tricks</div>
    </div>
  </div>

  <div class="logo-band">
    <span class="publisher-name">VORNA Education</span>
  </div>
</div>
</body>
</html>
```